Website for BrightlineLabs presentation

We need a new website, ideally as a wordpress there, for BrightlineLabs - we focus on machine learning, big data, data science and data analytics. This website should have two main sections - team presentation, introduction and offered services as static pages, and a blog section.

Target Market(s)

Companies which would like to hire the consultants for data science

Industry/Entity Type

Data Service

Font styles to use
Sans Serif

Colors

Designer to choose colors to be used in the design.

Requirements
Must have
• Wordpress template, blog and presentation pages, nice background images, incorporate the existing logo from brief
Nice to have
• match the word and ppt existing templates for brightline labs

```html
<!DOCTYPE html>
<html lang="en">
<head>
<meta charset="utf-8">
<title>Brightline Labs</title>
<link href="https://fonts.googleapis.com/css2?family=Arimo:wght@400;700&family=Lato:wght@400;700;900&display=swap" rel="stylesheet">
<style>
:root{
  --blue:#1b87c9;
  --blue-bright:#1aa3e8;
  --ink:#4a4a4a;
  --muted:#6b6b6b;
  --white:#ffffff;
  --night:#05080d;
  --navy:#0b1a2c;
  --frame:#1b7fc4;
}
*{margin:0;padding:0;box-sizing:border-box}
html,body{width:1200px;height:2866px;overflow:hidden}
body{font-family:"Lato",sans-serif;color:var(--ink);background:var(--white);position:relative}
section,header,footer{position:absolute;left:0;width:1200px}
.center{position:absolute;left:0;width:1200px;text-align:center}
.heading{font-family:"Arimo",sans-serif;font-weight:400;font-size:38px;color:var(--ink);letter-spacing:.3px}
.heading b{font-weight:700;color:var(--blue)}
.btn{position:absolute;left:527px;width:145px;height:50px;border-radius:25px;background:var(--blue);color:var(--white);font-weight:900;font-size:16px;display:flex;align-items:center;justify-content:center;letter-spacing:.3px}

/* hero */
.hero{top:0;height:625px;background:radial-gradient(ellipse at 45% 50%,#3a4350 0%,#1a1f27 45%,#07090c 100%)}
.hero-photo{position:absolute;inset:0}
.brand{position:absolute;left:76px;top:28px;display:flex;align-items:center;gap:10px;color:var(--white);font-weight:900;font-size:19px;line-height:20px;text-transform:uppercase}
.brand i{width:28px;height:28px;border-radius:50%;background:var(--white);display:block}
.nav{position:absolute;top:40px;left:608px;display:flex;gap:0;color:var(--white);font-size:16px}
.nav span{position:absolute;white-space:nowrap}
.hero-title{top:245px;font-family:"Arimo",sans-serif;font-size:42px;color:var(--white)}
.hero-title b{font-weight:700}
.hero-text{top:320px;left:290px;width:620px;font-size:16px;line-height:25px;color:var(--white)}
.hero .btn{top:407px;height:48px;width:145px}

/* about */
.about{top:625px;height:375px;background:var(--white)}
.about .heading{top:62px}
.about-text{top:133px;left:240px;width:720px;font-size:14.5px;line-height:26px;color:var(--muted)}
.about .btn{top:260px}

/* services */
.services{top:1000px;height:500px;background:radial-gradient(ellipse at 72% 45%,#153a66 0%,#0a1d35 35%,var(--night) 70%)}
.services .heading{top:62px;color:var(--white)}
.services .heading b{color:var(--white)}
.services-text{top:132px;left:270px;width:660px;font-size:15px;line-height:26px;color:var(--white)}
.service{position:absolute;top:240px;width:260px;text-align:center;color:var(--white)}
.service-icon{width:92px;height:92px;border-radius:50%;background:#8c8f94;border:4px solid #b7b9bc;margin:0 auto;display:flex;align-items:center;justify-content:center}
.service h3{margin-top:20px;font-size:18px;font-weight:900}
.service p{margin-top:6px;font-size:15px;line-height:27px}

/* testimonial */
.testimonial{top:1500px;height:522px;background:var(--white)}
.testimonial .heading{top:64px}
.quote-frame{position:absolute;left:0;top:0}
.quote-text{top:184px;left:340px;width:520px;font-size:15px;line-height:26.5px;color:var(--muted)}
.avatar{position:absolute;left:568px;top:354px;width:65px;height:65px;border:3px solid var(--blue);background:linear-gradient(160deg,#9fb4c6,#4d5d6d)}
.client{top:438px;font-weight:900;font-size:15px;color:var(--blue)}

/* newsletter */
.newsletter{top:2022px;height:290px;background:linear-gradient(90deg,#2c3038 0%,#4a4c52 45%,#6b6660 75%,#3d3b3a 100%)}
.newsletter .heading{top:64px;color:var(--white)}
.newsletter .heading b{color:var(--white)}
.news-sub{top:135px;font-size:15px;color:var(--white)}
.news-form{position:absolute;left:373px;top:178px;width:458px;height:50px;border:1px solid rgba(255,255,255,.85);border-radius:25px;background:rgba(0,0,0,.15)}
.news-form span{position:absolute;left:26px;top:15px;font-size:14px;font-style:italic;color:var(--white)}
.news-form b{position:absolute;right:-1px;top:-1px;width:145px;height:50px;border-radius:25px;background:var(--blue);color:var(--white);font-size:16px;font-weight:900;display:flex;align-items:center;justify-content:center}

/* blog */
.blog{top:2312px;height:377px;background:var(--white)}
.blog .heading{top:62px}
.post{position:absolute;top:138px;width:499px;height:170px;background:var(--white);box-shadow:0 2px 14px rgba(0,0,0,.14)}
.post-photo{position:absolute;left:0;top:0;width:260px;height:170px}
.post-date{position:absolute;left:0;top:105px;width:52px;height:65px;background:var(--blue-bright);color:var(--white);text-align:center;line-height:1}
.post-date b{display:block;font-size:30px;font-weight:400;margin-top:6px}
.post-date span{font-size:14px}
.post-body{position:absolute;left:272px;top:22px;width:215px}
.post-body h4{font-size:18px;font-weight:900;color:var(--blue-bright)}
.post-body p{margin-top:6px;font-size:14.5px;line-height:26px;color:var(--muted)}
.post-body em{display:block;margin-top:6px;font-style:normal;font-size:11px;font-weight:900;color:var(--blue-bright)}

/* footer */
.footer{top:2689px;height:177px;background:radial-gradient(ellipse at 35% 30%,#123a52 0%,#0a1f30 45%,#050d16 100%)}
.footer-links{position:absolute;left:80px;top:50px;font-size:15px;color:var(--white);word-spacing:2px}
.footer-links span{margin:0 17px}
.social{position:absolute;top:42px;width:34px;height:34px;border-radius:50%;background:#8a8e93}
.footer-rule{position:absolute;left:76px;top:114px;width:1046px;height:1px;background:rgba(255,255,255,.6)}
.copyright{top:134px;font-size:14.5px;color:var(--white)}
</style>
</head>
<body>

<header class="hero">
  <div class="hero-photo" role="img" aria-label="Dimmed photo of a team working at laptops with a faint network line overlay"></div>
  <div class="brand"><i></i><span>Brightline<br>Labs</span></div>
  <nav class="nav">
    <span style="left:0">Home</span>
    <span style="left:98px">About</span>
    <span style="left:200px">Services</span>
    <span style="left:314px">Blog</span>
    <span style="left:404px">Contact</span>
    <svg style="position:absolute;left:498px;top:0" width="20" height="20" viewBox="0 0 20 20" aria-label="Search"><circle cx="8" cy="8" r="6" fill="none" stroke="#fff" stroke-width="2"/><line x1="12.5" y1="12.5" x2="18" y2="18" stroke="#fff" stroke-width="2.4"/></svg>
  </nav>
  <h1 class="center hero-title"><b>BRIGHTLINE</b> LABS</h1>
  <p class="center hero-text">Lorem Ipsum is simply dummy text of the printing and typesetting industry. Lorem Ipsum has been the industry's standard dummy text ever since the 1500s</p>
  <a class="btn">CONTACT US</a>
</header>

<section class="about">
  <h2 class="center heading"><b>ABOUT</b> BRIGHTLINE LABS</h2>
  <p class="center about-text">Lorem Ipsum is simply dummy text of the printing and typesetting industry. Lorem Ipsum has been the industry's standard dummy text ever since the 1500s, when an unknown printer took a galley of type and scrambled it to make a type specimen book. It has survived not only five centuries, but also the leap into electronic typesetting, remaining PageMaker including versions of Lorem Ipsum.</p>
  <a class="btn">KNOW MORE</a>
</section>

<section class="services">
  <div style="position:absolute;inset:0" role="img" aria-label="Dark blue circuit board background"></div>
  <h2 class="center heading"><b>OUR</b> SERVICES</h2>
  <p class="center services-text">Lorem Ipsum is simply dummy text of the printing and typesetting industry. Lorem Ipsum has been the industry's standard dummy text ever since the 1500s, when an unknown printer took a galley of type and scrambled it to make a type specimen book.</p>
  <div class="service" style="left:63px">
    <div class="service-icon"><svg width="40" height="40" viewBox="0 0 40 40"><circle cx="20" cy="20" r="13" fill="none" stroke="#fff" stroke-width="2"/><circle cx="20" cy="20" r="4" fill="#fff"/></svg></div>
    <h3>Machine learning</h3><p>Lorem Ipsum is simply dummy<br>text typesetting industry.</p>
  </div>
  <div class="service" style="left:334px">
    <div class="service-icon"><svg width="40" height="40" viewBox="0 0 40 40"><circle cx="20" cy="20" r="13" fill="none" stroke="#fff" stroke-width="2"/><circle cx="20" cy="9" r="3" fill="#fff"/><circle cx="10" cy="26" r="3" fill="#fff"/><circle cx="30" cy="26" r="3" fill="#fff"/></svg></div>
    <h3>Big data</h3><p>Lorem Ipsum is simply dummy<br>text typesetting industry.</p>
  </div>
  <div class="service" style="left:606px">
    <div class="service-icon"><svg width="40" height="40" viewBox="0 0 40 40"><circle cx="20" cy="20" r="8" fill="none" stroke="#fff" stroke-width="2"/><circle cx="20" cy="20" r="15" fill="none" stroke="#fff" stroke-width="2" stroke-dasharray="5 4"/></svg></div>
    <h3>Data science</h3><p>Lorem Ipsum is simply dummy<br>text typesetting industry.</p>
  </div>
  <div class="service" style="left:877px">
    <div class="service-icon"><svg width="40" height="40" viewBox="0 0 40 40"><rect x="8" y="6" width="18" height="24" fill="none" stroke="#fff" stroke-width="2"/><circle cx="24" cy="24" r="6" fill="none" stroke="#fff" stroke-width="2"/><line x1="28" y1="28" x2="34" y2="34" stroke="#fff" stroke-width="3"/></svg></div>
    <h3>Data analytics</h3><p>Lorem Ipsum is simply dummy<br>text typesetting industry.</p>
  </div>
</section>

<section class="testimonial">
  <h2 class="center heading"><b>CLIENT</b> TESTIMONIAL</h2>
  <svg class="quote-frame" width="1200" height="522" viewBox="0 0 1200 522">
    <g stroke="var(--frame)" stroke-width="2" fill="none">
      <line x1="315" y1="153" x2="913" y2="153"/>
      <line x1="913" y1="134" x2="913" y2="311"/>
      <line x1="288" y1="170" x2="288" y2="330"/>
      <line x1="288" y1="312" x2="887" y2="312"/>
    </g>
    <text x="262" y="183" font-family="Georgia,serif" font-size="78" font-weight="700" fill="#555">&#8220;</text>
    <text x="888" y="350" font-family="Georgia,serif" font-size="78" font-weight="700" fill="#555">&#8221;</text>
    <polyline points="512,375 504,386 512,397" fill="none" stroke="var(--blue)" stroke-width="2.5"/>
    <polyline points="688,375 696,386 688,397" fill="none" stroke="var(--blue)" stroke-width="2.5"/>
  </svg>
  <p class="center quote-text">Lorem Ipsum is simply dummy text of the printing and typesetting industry. Lorem Ipsum has been the industry's standard dummy text ever since the 1500s, when an unknown printer took a galley of type and scrambled it to make a type specimen book.</p>
  <div class="avatar" role="img" aria-label="Client portrait photo"></div>
  <p class="center client">- Client Name</p>
</section>

<section class="newsletter">
  <div style="position:absolute;inset:0" role="img" aria-label="Dimmed photo of colleagues in an office"></div>
  <h2 class="center heading"><b>NEWS</b>LETTER</h2>
  <p class="center news-sub">For latest news or updates subscribe our newsletter</p>
  <div class="news-form"><span>Enter e-mail here...</span><b>SUBSCRIBE</b></div>
</section>

<section class="blog">
  <h2 class="center heading"><b>RECENT</b> BLOG</h2>
  <article class="post" style="left:76px">
    <div class="post-photo" role="img" aria-label="Photo of a hand with a pen over data charts" style="background:linear-gradient(135deg,#d9c9b0,#6b7d8e 60%,#2e3c4a)"></div>
    <div class="post-date"><b>20</b><span>Apr</span></div>
    <div class="post-body"><h4>Lorem Ipsum is simply</h4><p>Lorem Ipsum is simply dummy text of the printing and typesetting industry.</p><em>READ MORE...</em></div>
  </article>
  <article class="post" style="left:623px">
    <div class="post-photo" role="img" aria-label="Photo of a tablet showing business charts" style="background:linear-gradient(135deg,#eef2f6,#a9b8c6 55%,#5d7188)"></div>
    <div class="post-date"><b>20</b><span>Apr</span></div>
    <div class="post-body"><h4>Lorem Ipsum is simply</h4><p>Lorem Ipsum is simply dummy text of the printing and typesetting industry.</p><em>READ MORE...</em></div>
  </article>
</section>

<footer class="footer">
  <div class="footer-links">Home<span>|</span>About<span>|</span>Services<span>|</span>Blog<span>|</span>Contact</div>
  <div class="social" style="left:996px"></div>
  <div class="social" style="left:1042px"></div>
  <div class="social" style="left:1088px"></div>
  <div class="footer-rule"></div>
  <p class="center copyright">© <b>BRIGHTLINE LABS</b> - 2018. All Rights Reserved.</p>
</footer>

</body>
</html>
```